TA BRAMLEY BUSINESS CARD DESIGN PROJECT

We need to utilize our logo that was expertly created on PixelHarbor and now need to match this with a business card design.

```html
<!DOCTYPE html>
<html lang="en">
<head>
<meta charset="utf-8">
<title>TA BRAMLEY Business Card</title>
<link href="https://fonts.googleapis.com/css2?family=Open+Sans:wght@400;600;700&display=swap" rel="stylesheet">
<style>
  :root {
    --stage: #242424;
    --glow: #4a4848;
    --brand-blue: #1558a6;
    --bar-left: #36639f;
    --bar-right: #1565b3;
    --cream: #f8f9e3;
    --butter: #fef8e3;
    --sky: #d6ecf9;
    --white: #ffffff;
    --ink: #1a1a1a;
    --rule: #555555;
  }
  * { margin: 0; padding: 0; box-sizing: border-box; }
  html, body { width: 1200px; height: 780px; overflow: hidden; }
  body {
    position: relative;
    background: var(--stage);
    font-family: "Open Sans", Arial, sans-serif;
  }
  .stage-glow {
    position: absolute;
    left: 310px; top: 373px; width: 579px; height: 34px;
    background: radial-gradient(ellipse 50% 100% at 50% 50%, var(--glow), var(--stage));
  }
  .card {
    position: absolute;
    left: 310px; width: 579px; height: 330px;
    overflow: hidden;
  }
  .card--front { top: 43px; background: var(--brand-blue); }
  .card--back { top: 407px; background: var(--white); }

  .brand-name {
    position: absolute;
    font-weight: 700;
    white-space: nowrap;
    transform: translate(-50%, -50%);
    letter-spacing: 0.04em;
  }
  .card--front .brand-name { left: 50%; top: 50%; font-size: 52px; color: var(--white); }
  .card--back .brand-name { left: 144px; top: 164px; font-size: 32px; color: var(--brand-blue); }

  .stripe { position: absolute; top: 0; height: 100%; }
  .stripe--cream { left: 0; width: 33px; background: var(--cream); }
  .stripe--butter { left: 256px; width: 33px; background: var(--butter); }
  .stripe--sky-mid { left: 289px; width: 33px; background: var(--sky); }
  .stripe--sky-edge { left: 546px; width: 33px; background: var(--sky); }

  .edge-bar { position: absolute; top: 82px; width: 13px; height: 166px; }
  .edge-bar--left { left: 0; background: var(--bar-left); }
  .edge-bar--right { left: 566px; background: var(--bar-right); }

  .divider {
    position: absolute; left: 287px; top: 73px;
    width: 1px; height: 185px; background: var(--rule);
  }

  .contact-person { position: absolute; left: 324px; top: 88px; }
  .contact-person__name {
    font-size: 29px; font-weight: 700; color: var(--brand-blue);
    line-height: 36px; white-space: nowrap;
  }
  .contact-person__role { font-size: 15px; font-weight: 600; color: var(--ink); line-height: 18px; }

  .contact-list {
    position: absolute; left: 324px; top: 160px; list-style: none;
  }
  .contact-list li {
    display: flex; align-items: center; height: 20.3px;
    font-size: 15.5px; color: var(--ink); white-space: nowrap;
  }
  .contact-list svg { width: 13px; height: 13px; margin-right: 8px; flex: none; }

  .address {
    position: absolute; left: 0; width: 579px; top: 276px;
    text-align: center; font-size: 15.5px; color: var(--ink);
  }
</style>
</head>
<body>
  <div class="stage-glow"></div>

  <section class="card card--front">
    <div class="brand-name">TA BRAMLEY</div>
  </section>

  <section class="card card--back">
    <div class="stripe stripe--cream"></div>
    <div class="stripe stripe--butter"></div>
    <div class="stripe stripe--sky-mid"></div>
    <div class="stripe stripe--sky-edge"></div>
    <div class="edge-bar edge-bar--left"></div>
    <div class="edge-bar edge-bar--right"></div>

    <div class="brand-name">TA BRAMLEY</div>
    <div class="divider"></div>

    <div class="contact-person">
      <div class="contact-person__name">Marcus T. Ellery</div>
      <div class="contact-person__role">Owner</div>
    </div>

    <ul class="contact-list">
      <li>
        <svg viewBox="0 0 12 12"><rect x="3" y="0.7" width="6" height="10.6" rx="1" fill="none" stroke="#1558a6" stroke-width="1.2"/></svg>
        555-213-4780
      </li>
      <li>
        <svg viewBox="0 0 12 12"><path d="M2 1.5 L4 1 L5 3.5 L3.8 4.5 Q4.8 7 7.5 8.2 L8.5 7 L11 8 L10.5 10 Q5 11 1.5 5 Z" fill="#1558a6"/><path d="M7 1.5 A3.5 3.5 0 0 1 10.5 5" fill="none" stroke="#1558a6"/></svg>
        555-318-2094
      </li>
      <li>
        <svg viewBox="0 0 12 12"><circle cx="6" cy="6" r="5.5" fill="#1558a6"/><path d="M3 3 Q5 4 4 6 Q6 8 5 10 M8 2 Q7 4 9 5" fill="none" stroke="#fff" stroke-width="1"/></svg>
        www.tabramley.com
      </li>
      <li>
        <svg viewBox="0 0 12 12"><path d="M0.5 5 L6 1 L11.5 5 V11.5 H0.5 Z" fill="#1558a6"/><rect x="2.5" y="3" width="7" height="4.5" fill="#fff"/><path d="M0.5 5 L6 9 L11.5 5" fill="none" stroke="#fff" stroke-width="0.8"/></svg>
        marcusellery@tabramley.com
      </li>
    </ul>

    <p class="address">240 W Harbor St Cedar Bend, Wi 54021</p>
  </section>
</body>
</html>
```